UI Improvement for FlorKeep app

We are looking for a talented UI/UX designer to REFINE and enhance the visual design of our mobile application, FlorKeep. The app is fully functional, but we need a designer to improve its aesthetics by specifying design elements such as fonts, colors, spacing, and component styles.
Your task will be to analyze the CURRENT UI and provide detailed design specifications that will make the app more visually appealing, modern, and user-friendly.
TODO:
Review the existing FlorKeep app design (see attachments) and identify areas for visual improvement.
Provide a detailed UI style guide, including:
Typography (font choices, sizes, and weights)
Color palette (primary, secondary, and accent colors)
Component styling (buttons, forms, icons, and interactive elements)
Spacing and layout guidelines (margins, paddings, and alignment)
Ensure the design remains clean, modern, and professional while maintaining usability and accessibility.
Provide design mockups or visual examples (if possible) to illustrate the proposed changes.
Deliverables:
A UI Style Guide (PDF or Figma file) with specifications on fonts, colors, spacing, and UI components.
Optionally, before/after mockups or examples demonstrating the improvements.
Ideal Designer:
Strong experience in mobile UI/UX design.
Understanding of modern design trends and best practices.
Ability to communicate design choices clearly for easy developer implementation.
I have attached 7 images showcasing the main UI screens used in the FlorKeep app. These screens need visual enhancements to improve their overall look and user experience.
The images represent the current design in three key modes:
LIST Mode – Displays data in a structured list format.
READ Mode – Shows detailed information when a user selects an item.
ADD/EDIT Mode – Allows users to input or modify information.
Additionally, there is a ‘MORE’ page, which serves as a menu listing other features of the application.
Task Objective:
Please refine and improve these UIs to create a more modern, visually appealing, and user-friendly experience. Focus on typography, colors, spacing, and component styling to ensure a cohesive and polished design.
Look and feel
Each slider illustrates characteristics of the customer's brand and the style your logo design should communicate.

```html
<!DOCTYPE html>
<html lang="en">
<head>
<meta charset="utf-8">
<title>FlorKeep – Contact and Pilots screens</title>
<link href="https://fonts.googleapis.com/css2?family=Bree+Serif&family=Lato:wght@400;700&display=swap" rel="stylesheet">
<style>
:root{
  --canvas:#ececec;
  --header:#27a2d4;
  --nav:#20b29a;
  --accent:#1ba589;
  --panel:#f8f8f9;
  --field:#ffffff;
  --field-line:#eeeeee;
  --text:#3a3a3a;
  --muted:#8a8a8a;
  --divider:#d9d9d9;
  --pilots-card:#e3f2f8;
  --owner-card:#e5f5f2;
  --title-blue:#2596c6;
  --avatar:#8fa6ba;
}
*{box-sizing:border-box;margin:0;padding:0}
html,body{width:1200px;height:828px;overflow:hidden;background:var(--canvas)}
body{position:relative;font-family:"Lato",sans-serif;color:var(--text)}
.screen{position:absolute;width:357px;height:772px;background:#fff;overflow:hidden}
.screen--contact-edit{left:15px;top:12px}
.screen--pilots{left:428px;top:34px;width:343px;height:744px;border-radius:26px}
.screen--contact-read{left:816px;top:12px}

.header{position:absolute;left:0;top:0;width:100%;height:113px;background:var(--header);
  clip-path:polygon(0 0,100% 0,100% 74%,calc(100% - 42px) 100%,0 100%)}
.screen--pilots .header{height:165px;clip-path:polygon(0 0,100% 0,100% 75%,calc(100% - 46px) 100%,0 100%)}
.status-time{position:absolute;left:28px;top:9px;color:#fff;font-size:12px}
.screen--pilots .status-time{left:33px;top:19px}
.status-icons{position:absolute;right:14px;top:11px}
.screen--pilots .status-icons{top:20px;right:12px}
.title{position:absolute;color:#fff;font-family:"Bree Serif",serif;font-size:29px;letter-spacing:.5px}
.screen--contact-edit .title{left:26px;top:53px}
.screen--contact-read .title{left:0;width:100%;text-align:center;top:47px}
.screen--pilots .title{left:26px;top:44px;font-size:27px}
.header-actions{position:absolute;display:flex;gap:10px;align-items:center}
.back{position:absolute;left:27px;top:66px}

.panel{position:absolute;left:26px;width:306px;background:var(--panel);border-radius:6px}
.field{position:absolute;left:11px;width:285px;height:33px;background:var(--field);border:1px solid var(--field-line);
  border-radius:17px;font-size:8px;padding-left:16px;display:flex;align-items:center;box-shadow:0 1px 2px rgba(0,0,0,.03)}
.field .end{position:absolute;right:14px;top:50%;transform:translateY(-50%)}
.required{position:absolute;left:12px;font-size:8px;color:var(--accent)}

.search{position:absolute;left:26px;top:89px;width:285px;height:33px;background:#fff;border-radius:17px;
  display:flex;align-items:center;padding-left:13px;font-size:11px}
.search span{margin-left:11px}
.search a{position:absolute;right:12px;font-size:8.5px;color:var(--accent);text-decoration:underline}

.pilot-row{position:absolute;left:0;width:100%;height:60px}
.avatar{position:absolute;border-radius:50%;background:radial-gradient(circle at 50% 40%,#c9d6e2,var(--avatar) 70%,#5e7388)}
.pilot-row .avatar{left:25px;top:3px;width:53px;height:53px}
.pilot-name{position:absolute;left:101px;top:18px;font-size:8.5px;line-height:15px}
.pilot-date{position:absolute;left:255px;top:16px;font-size:8.5px;display:flex;gap:6px;align-items:center}
.pilot-row .rule{position:absolute;left:97px;width:212px;top:59px;border-top:1.5px solid var(--divider)}
.pilot-row--fade{opacity:.35}

.nav{position:absolute;left:0;bottom:0;width:100%;height:78px;background:var(--nav);
  clip-path:polygon(0 36px,46px 0,100% 0,100% 100%,0 100%)}
.screen--pilots .nav{height:69px;clip-path:polygon(0 30px,42px 0,calc(100% - 16px) 0,100% 14px,100% 100%,0 100%)}
.nav-item{position:absolute;top:22px;width:60px;margin-left:-30px;text-align:center;color:#fff;font-size:8px}
.screen--pilots .nav-item{top:20px}
.nav-item svg{display:block;margin:0 auto 7px}
.nav-item--active{font-weight:700}

.card{position:absolute;left:24px;width:306px;border-radius:6px}
.card-title{position:absolute;left:23px;font-family:"Bree Serif",serif;font-size:14px;color:var(--title-blue)}
.collapse{position:absolute;right:6px;top:12px;font-family:"Bree Serif",serif;font-size:9px;color:var(--accent)}
.card-text{position:absolute;left:25px;font-size:8.5px;line-height:18px}
</style>
</head>
<body>
<svg width="0" height="0" style="position:absolute">
  <defs>
    <symbol id="signal" viewBox="0 0 48 12"><rect x="0" y="8" width="3" height="4" fill="#fff"/><rect x="4" y="6" width="3" height="6" fill="#fff"/><rect x="8" y="3" width="3" height="9" fill="#fff"/><rect x="12" y="0" width="3" height="12" fill="#fff"/><path d="M19 4a9 9 0 0 1 12 0M21.5 6.5a5 5 0 0 1 7 0" stroke="#fff" stroke-width="1.6" fill="none"/><circle cx="25" cy="9.5" r="1.4" fill="#fff"/><rect x="34" y="2" width="12" height="8" rx="2" fill="none" stroke="#fff" stroke-width="1.2"/><rect x="35.5" y="3.5" width="9" height="5" fill="#fff"/><rect x="46.2" y="4.5" width="1.5" height="3" fill="#fff"/></symbol>
    <symbol id="dots" viewBox="0 0 24 6"><circle cx="3" cy="3" r="2.6" fill="#fff"/><circle cx="12" cy="3" r="2.6" fill="#fff"/><circle cx="21" cy="3" r="2.6" fill="#fff"/></symbol>
    <symbol id="field-dots" viewBox="0 0 18 4"><circle cx="2" cy="2" r="1.5" fill="#999"/><circle cx="9" cy="2" r="1.5" fill="#999"/><circle cx="16" cy="2" r="1.5" fill="#999"/></symbol>
    <symbol id="plus" viewBox="0 0 14 14"><circle cx="7" cy="7" r="7" fill="var(--accent)"/><path d="M7 3.5v7M3.5 7h7" stroke="#fff" stroke-width="1.8"/></symbol>
    <symbol id="calendar" viewBox="0 0 12 12"><rect x=".6" y="1.6" width="10.8" height="9.8" fill="none" stroke="#9a9a9a" stroke-width="1"/><path d="M.6 4h10.8M3 .5v2M9 .5v2M3.5 4v7.4M6 4v7.4M8.5 4v7.4M.6 6.5h10.8M.6 9h10.8" stroke="#9a9a9a" stroke-width=".6"/></symbol>
    <symbol id="nav-contact" viewBox="0 0 24 24"><circle cx="12" cy="12" r="12" fill="#fff"/><circle cx="12" cy="9.5" r="3.6" fill="var(--nav)"/><path d="M5.5 18.5a6.5 5 0 0 1 13 0z" fill="var(--nav)"/></symbol>
    <symbol id="nav-pilot" viewBox="0 0 24 24"><circle cx="12" cy="12" r="12" fill="#fff"/><path d="M7 7.5l5-2 5 2-5 1.6z" fill="var(--nav)"/><circle cx="12" cy="11.3" r="2.8" fill="var(--nav)"/><path d="M6 19a6 4.6 0 0 1 12 0z" fill="var(--nav)"/></symbol>
    <symbol id="nav-plane" viewBox="0 0 24 24"><circle cx="12" cy="12" r="12" fill="#fff"/><path d="M11 4.5h2v5.5l6 3v1.6l-6-1.6v3.5l2 1.5v1.2l-3-.8-3 .8V18l2-1.5V13l-6 1.6V13l6-3z" fill="var(--nav)"/></symbol>
    <symbol id="nav-request" viewBox="0 0 24 24"><circle cx="8" cy="9" r="3.3" fill="#fff"/><path d="M1.5 20a6.5 5.5 0 0 1 13 0z" fill="#fff"/><circle cx="17" cy="7" r="5.5" fill="#fff"/><path d="M15.3 5.8a1.8 1.8 0 1 1 2.4 1.7c-.5.2-.7.5-.7 1v.5" stroke="var(--nav)" stroke-width="1.3" fill="none"/><circle cx="17" cy="10" r=".8" fill="var(--nav)"/></symbol>
    <symbol id="nav-more" viewBox="0 0 24 24"><circle cx="12" cy="12" r="12" fill="#fff"/><circle cx="7" cy="12" r="1.9" fill="var(--nav)"/><circle cx="12" cy="12" r="1.9" fill="var(--nav)"/><circle cx="17" cy="12" r="1.9" fill="var(--nav)"/></symbol>
  </defs>
</svg>

<!-- Contact: add / edit -->
<section class="screen screen--contact-edit">
  <header class="header">
    <span class="status-time">9:30</span>
    <svg class="status-icons" width="58" height="13"><use href="#signal"/></svg>
    <h1 class="title">Contact</h1>
    <div class="header-actions" style="left:284px;top:68px">
      <svg width="12" height="16" viewBox="0 0 12 16"><path d="M0 0h12v16l-6-4.5L0 16z" fill="#fff"/></svg>
      <svg width="22" height="6"><use href="#dots"/></svg>
    </div>
  </header>
  <div class="panel" style="top:130px;height:207px">
    <div class="field" style="top:20px">Business Name -e<svg class="end" width="18" height="4"><use href="#field-dots"/></svg></div>
    <div class="field" style="top:62px">First Name - e</div>
    <div class="field" style="top:103px">Middle Name - e</div>
    <div class="field" style="top:145px">Last Name - e</div>
  </div>
  <div class="panel" style="top:345px;height:326px">
    <svg style="position:absolute;right:11px;top:13px" width="9" height="6" viewBox="0 0 9 6"><path d="M1 5l3.5-3.5L8 5" stroke="#444" stroke-width="1.3" fill="none"/></svg>
    <div class="field" style="top:31px">Address Lable Tag -e<svg class="end" width="18" height="4"><use href="#field-dots"/></svg></div>
    <span class="required" style="top:76px">Required</span>
    <div class="field" style="top:90px">AddressLine 1 -e</div>
    <span class="required" style="top:128px">Required</span>
    <div class="field" style="top:142px">AddressLine 2 -e</div>
    <div class="field" style="top:185px">Address City<svg class="end" width="7" height="11" viewBox="0 0 7 11"><path d="M3.5 0L7 4H0zM3.5 11L0 7h7z" fill="#aaa"/></svg></div>
    <div class="field" style="top:229px">Address State</div>
    <div class="field" style="top:272px">Zip - e</div>
  </div>
  <nav class="nav">
    <div class="nav-item nav-item--active" style="left:57px"><svg width="24" height="24"><use href="#nav-contact"/></svg>Contact</div>
    <div class="nav-item" style="left:116px"><svg width="24" height="24"><use href="#nav-pilot"/></svg>Pilot</div>
    <div class="nav-item" style="left:180px"><svg width="24" height="24"><use href="#nav-plane"/></svg>Plane</div>
    <div class="nav-item" style="left:245px"><svg width="24" height="24"><use href="#nav-request"/></svg>Fit Request</div>
    <div class="nav-item" style="left:309px"><svg width="24" height="24"><use href="#nav-more"/></svg>More...</div>
  </nav>
</section>

<!-- Pilots: list -->
<section class="screen screen--pilots">
  <header class="header">
    <span class="status-time">9:30</span>
    <svg class="status-icons" width="58" height="13"><use href="#signal"/></svg>
    <h1 class="title">Pilots</h1>
    <div class="header-actions" style="left:265px;top:52px">
      <svg width="14" height="14" viewBox="0 0 14 14"><circle cx="7" cy="7" r="7" fill="#fff"/><path d="M7 3.5v7M3.5 7h7" stroke="var(--header)" stroke-width="1.8"/></svg>
      <svg width="22" height="6"><use href="#dots"/></svg>
    </div>
    <div class="search">
      <svg width="14" height="14" viewBox="0 0 14 14"><circle cx="6" cy="6" r="4.8" stroke="#777" stroke-width="1.3" fill="none"/><path d="M9.5 9.5L13 13" stroke="#777" stroke-width="1.3"/></svg>
      <span>Search</span><a>Advanced Search</a>
    </div>
  </header>
  <div class="pilot-row" style="top:180px"><div class="avatar" role="img" aria-label="Pilot portrait"></div><div class="pilot-name">Abbott, Carl, Bryce, 3<br>182133,</div><div class="pilot-date"><svg width="12" height="12"><use href="#calendar"/></svg>9/30/24</div><div class="rule"></div></div>
  <div class="pilot-row" style="top:247px"><div class="avatar" role="img" aria-label="Pilot portrait"></div><div class="pilot-name">Bellamy, Rowan<br>4467155</div><div class="pilot-date"><svg width="12" height="12"><use href="#calendar"/></svg>2/28/25</div><div class="rule"></div></div>
  <div class="pilot-row" style="top:313px"><div class="avatar" role="img" aria-label="Pilot portrait"></div><div class="pilot-name">Brightwell, Aron<br>2663187</div><div class="pilot-date"><svg width="12" height="12"><use href="#calendar"/></svg>10/30/24</div><div class="rule"></div></div>
  <div class="pilot-row" style="top:380px"><div class="avatar" role="img" aria-label="Pilot portrait in cockpit"></div><div class="pilot-name">Corri, Ada, Simon<br>4360575</div><div class="pilot-date"><svg width="12" height="12"><use href="#calendar"/></svg>3/30/25,</div><div class="rule"></div></div>
  <div class="pilot-row" style="top:447px"><div class="avatar" role="img" aria-label="Pilot portrait"></div><div class="pilot-name">Cruz Galvan,<br>182133,</div><div class="pilot-date"><svg width="12" height="12"><use href="#calendar"/></svg>9/30/24</div><div class="rule"></div></div>
  <div class="pilot-row" style="top:513px"><div class="avatar" role="img" aria-label="Pilot portrait"></div><div class="pilot-name">Garrett, Cole,<br>3423819</div><div class="pilot-date"><svg width="12" height="12"><use href="#calendar"/></svg>2/28/25,</div><div class="rule"></div></div>
  <div class="pilot-row" style="top:580px"><div class="avatar" role="img" aria-label="Pilot portrait"></div><div class="pilot-name">Gibbs, Jonah, Alden<br>2761635</div><div class="pilot-date"><svg width="12" height="12"><use href="#calendar"/></svg>3/6/23</div><div class="rule"></div></div>
  <div class="pilot-row pilot-row--fade" style="top:646px"><div class="avatar" role="img" aria-label="Pilot portrait"></div><div class="pilot-name">Gibbs, Jonah, Alden<br>2761635</div><div class="pilot-date"><svg width="12" height="12"><use href="#calendar"/></svg>3/6/23</div></div>
  <nav class="nav">
    <div class="nav-item" style="left:50px"><svg width="22" height="22"><use href="#nav-contact"/></svg>Contact</div>
    <div class="nav-item nav-item--active" style="left:109px"><svg width="22" height="22"><use href="#nav-pilot"/></svg>Pilot</div>
    <div class="nav-item" style="left:168px"><svg width="22" height="22"><use href="#nav-plane"/></svg>Plane</div>
    <div class="nav-item" style="left:230px"><svg width="22" height="22"><use href="#nav-request"/></svg>Fit Request</div>
    <div class="nav-item" style="left:289px"><svg width="22" height="22"><use href="#nav-more"/></svg>More...</div>
  </nav>
</section>

<!-- Contact: read -->
<section class="screen screen--contact-read">
  <header class="header">
    <span class="status-time">9:30</span>
    <svg class="status-icons" width="58" height="13"><use href="#signal"/></svg>
    <svg class="back" width="20" height="12" viewBox="0 0 20 12"><path d="M19 6H2M7 1L2 6l5 5" stroke="#fff" stroke-width="1.6" fill="none"/></svg>
    <h1 class="title">Contact</h1>
    <div class="header-actions" style="left:307px;top:70px"><svg width="22" height="6"><use href="#dots"/></svg></div>
  </header>
  <div class="panel" style="top:130px;height:319px">
    <div class="field" style="top:21px">Add Email -e<svg class="end" width="13" height="13"><use href="#plus"/></svg></div>
    <div class="field" style="top:61px">Add Social Media - e<svg class="end" width="13" height="13"><use href="#plus"/></svg></div>
    <div class="field" style="top:101px">Add Emergency Contact- e<svg class="end" width="13" height="13"><use href="#plus"/></svg></div>
    <div class="field" style="top:140px">Add Personal Information- e<svg class="end" width="13" height="13"><use href="#plus"/></svg></div>
    <div class="field" style="top:180px">Add Work Info- e<svg class="end" width="13" height="13"><use href="#plus"/></svg></div>
    <div class="field" style="top:220px">Add Skills / Talents - e<svg class="end" width="13" height="13"><use href="#plus"/></svg></div>
    <div class="field" style="top:260px">Add Resources - e<svg class="end" width="13" height="13"><use href="#plus"/></svg></div>
  </div>
  <div class="card" style="top:459px;height:113px;background:var(--pilots-card)">
    <h2 class="card-title" style="top:14px">Pilots –e</h2>
    <span class="collapse">Collapse</span>
    <div class="avatar" role="img" aria-label="Pilot portrait" style="left:18px;top:44px;width:43px;height:43px"></div>
    <div class="card-text" style="left:75px;top:50px;line-height:15px">Alder, Quinn<br>3647946</div>
    <div style="position:absolute;left:208px;top:53px;font-size:8.5px;display:flex;gap:6px;align-items:center"><svg width="12" height="12"><use href="#calendar"/></svg>10/31/23</div>
    <svg style="position:absolute;left:284px;top:56px" width="9" height="6" viewBox="0 0 9 6"><path d="M1 1l3.5 3.5L8 1" stroke="#333" stroke-width="1.3" fill="none"/></svg>
    <div style="position:absolute;left:22px;right:6px;top:97px;border-top:2px solid #d3ebf3"></div>
  </div>
  <div class="card" style="top:582px;height:93px;background:var(--owner-card)">
    <h2 class="card-title" style="top:14px">Aircraft Owner –e</h2>
    <span class="collapse">Collapse</span>
    <p class="card-text" style="top:35px">Personal: Alder, Quinn: Aerolark: A40: Aerolark Aircraft<br>Company, Single Engine, 1100</p>
    <div style="position:absolute;left:22px;right:6px;top:80px;border-top:2px solid #d6eeea"></div>
  </div>
  <nav class="nav">
    <div class="nav-item nav-item--active" style="left:57px"><svg width="24" height="24"><use href="#nav-contact"/></svg>Contact</div>
    <div class="nav-item" style="left:116px"><svg width="24" height="24"><use href="#nav-pilot"/></svg>Pilot</div>
    <div class="nav-item" style="left:180px"><svg width="24" height="24"><use href="#nav-plane"/></svg>Plane</div>
    <div class="nav-item" style="left:245px"><svg width="24" height="24"><use href="#nav-request"/></svg>Fit Request</div>
    <div class="nav-item" style="left:309px"><svg width="24" height="24"><use href="#nav-more"/></svg>More...</div>
  </nav>
</section>
</body>
</html>
```